UI design for an Zyn(Halvo) photo editing app

This design contest is to design the UI/screenshots of an Zyn(Halvo) app named "Kestrel Pix". Some minor design details are left out at this point as the mockup is still in progress. The icon of this app will be designed separately. The winner of this job will be selected to work on a long term basis as an Dorvo version and several updates will have to be designed as well as the Quillex version. Please take
this as a long term opportunity.
The photo app is called "Kestrel Pix". The design need to dynamic, different that stands out WITH a serious and polished look.
All the mockups and sample screenshots are attached for ease. Please thoroughly review them.
This app has the following screens:
1. Welcome screen(just a simple background will do now as icon will be put later).
2. Main Screen (or LightBox)
The background of this screen can be the same as the background of the welcome screen. It can be a wooden background OR a background of your
choice that fits and blends in the buttons and fonts/colors.
The main screen has this bars/buttons/options that has separate screens:
On top, menu bar:
has these buttons
settings on the left(icon)
in the middle, 3 buttons (please check lightbox mockup and lightbox sample pics)
on the right, share icon(check share screen sample)
Our share options:
"Share" button screenshot:
Our share options:
Save
Email
Copy
Moodlefy
Chatterbay
Zorbly
Quorra
in the middle, just background where the pictures would appear later after importing
or saving
at the bottom bar:
3 buttons:
Camera Roll(on the left)
Camera Button(middle)
Advanced Button(on the right)
2 versions of this screenshot need to be designed.
1. regular version with all the options
2. regular version plus the "steam effect" button showing up on top of the "Advanced" button(mockup with red lines)
3 separate screenshots need to be designed for the options"
settings screenshot(please check sample):
Gift Kestrel Pix to a friend
Rate/review in the Tundle Hub
(space in between...so they are grouped)
Geotagiing(on/off)
Captured photos get location-specific information(these lines in smaller fonts)
Launch in Capture Mode(on/off)
Kestrel Pix is automatically lauched in camera mode
Autosave to Camera Roll(on/off)
Captured photos are directly saved to camera roll
Reset All Tutorials
Tap to reset all the tutorials
In the "Steam Effect" screen, please check the mockup
Top Bar: lightbox button(to go back), heading and Done button
Middle: Steam background(provided)
Bottom bar:
refresh button
droplets(when clicked on/off options show up on top, please check mockup)
finger size(when clicked 3 options show up)
steam density(when clicked 3 options show up)
Please use the buttons for the droplets, finger size and steam density from the steam effects button image provided)
(and also the background of this screenshot(in the middle) would be a steam screen which is provided. Please use the
steam background provided and you need to use the background in the middle, just omit the top and the bottom bar from the image)
Now back to the main(lightbox screen):
When Clicked on the "Camera" in the middle of the bottom bar, the capture mode screen shows up.
Please refer to the mockup first
There you will see the cancel button on the left
camera button in the middle
a small settings button on the right
and a filters button on the right
and the filters bar on the top
ours need to like this
please refer to capture mode sample 1
please refer to capture mode sample 2
please refer to capture mode sample 3
normal
Grid
timer(5/15/30 secs)
Edit Screen(check sample)
Edit options
Adjust:(displayed on a bar)
1. Left
2. Right
3. Horizontal
4. Vertical
5. Straightening
Crop:
None
Original
Golden
Freeform
Square
3:2
4:3
4:6
5:7
8:10
16:9
Filters:(please note that this filter icon and the filter icon in the "capture mode" screenshot need to same)
(the filters are displayed on a bar, please check sample)
There is a sample picture that you need to put in the picture of the filters. It would be same picture in
every filter at this point.
00.None
0.Calibrate
1. aurora
2. drizzle
3. icicle
4. blizzard
5. calm
6. dew
7. knot
8. dry
9. eye
10. flurry
11. fog
12. frost
13. hail
14. haze
15. heat
16. humid
17. overcast
18. polar
19. thermal
20. trace
Editing options on top:(check sample)
Brightness
Contrast
Saturation
Textures:(dispalyed on a bar, check sample)
1.None
2.Bark
3.Grunge1
4.Grunge2
5.grunge3
6.Grunge4
7.Paper
8.Cardboard
9.Wood
10.Bokeh
11.Bricks
12.Metal
13.Asphalt
14.Pavement1
15.Pavement2
16.Paint1
17.Paint2
18.Rust
19.Towel
20.Stone1
21.Stone2
22.Wall
23.Urban1
24.Urban2
25.Urban3
26.Watercolor
Tilt-shift/Vignette:(check sample)
Borders:(check samples, at this point, we are working on them, you just need to make a bar that displays them)
1.None
2.
3.
4.
5.
6.
7.
8.
9.
10.
11.
12.
13.
14.
15.
16.
This is our primary design mockup. Upon selecting the final version, we will be working on some more and minor details(as
we are also working with the coders).
And there is a folder callled "app sample". Please take a look at it and think how our app can be different and stand out.
Thanks and feel free to contact me anytime if you have any questions. Looking forward to hearing from you and building a long term
relationship.
All camera app users who likes to edit their photos with cool tools.
Building

```html
<!DOCTYPE html>
<html lang="en">
<head>
<meta charset="utf-8">
<title>Kestrel Pix – Capture Mode</title>
<link rel="stylesheet" href="https://fonts.googleapis.com/css2?family=PT+Sans:wght@400;700&display=swap">
<style>
  :root {
    --frame-dark: #141414;
    --bar-red: #a90f18;
    --bar-red-deep: #7e0910;
    --bar-red-light: #c4222b;
    --stitch: rgba(255,255,255,0.35);
    --grid-line: rgba(255,255,255,0.7);
    --label-light: #e6ebef;
    --track-light: #f2f2f2;
    --track-red: #c8121c;
    --icon-silver: #e3e6ea;
    --button-text: #8a0a12;
  }
  * { box-sizing: border-box; margin: 0; padding: 0; }
  html, body { width: 676px; height: 1200px; overflow: hidden; background: var(--frame-dark); }
  body { font-family: "PT Sans", Arial, sans-serif; }
  .capture-screen { position: relative; width: 676px; height: 1200px; overflow: hidden; }

  .viewfinder {
    position: absolute; left: 0; top: 0; width: 676px; height: 1062px;
    background:
      linear-gradient(180deg, rgba(120,40,30,0.35) 0%, rgba(0,0,0,0) 12%),
      linear-gradient(90deg, #b9bdb8 0%, #cfd1cc 30%, #2a2b2e 34%, #1d1e22 70%, #3b3a3e 100%);
  }
  .viewfinder-grid { position: absolute; left: 0; top: 0; width: 676px; height: 1062px; }

  .grid-status {
    position: absolute; left: 0; width: 676px; top: 830px; text-align: center;
    font-size: 34px; font-weight: 700; color: var(--label-light); letter-spacing: 0.5px;
    text-shadow: 0 2px 3px rgba(0,0,0,0.7);
  }

  .zoom-control { position: absolute; left: 0; top: 962px; width: 676px; height: 36px; }
  .zoom-value {
    position: absolute; left: 35px; top: 4px; font-size: 22px; font-weight: 700;
    color: var(--label-light); text-shadow: 0 1px 2px rgba(0,0,0,0.8);
  }
  .zoom-track {
    position: absolute; left: 100px; top: 4px; width: 535px; height: 28px; border-radius: 14px;
    background: linear-gradient(180deg, #ffffff, #c9c9c9); box-shadow: 0 1px 3px rgba(0,0,0,0.6);
  }
  .zoom-track-fill {
    position: absolute; left: 175px; right: 8px; top: 8px; height: 12px; border-radius: 6px;
    background: var(--track-red);
  }
  .zoom-track-empty {
    position: absolute; left: 8px; width: 170px; top: 8px; height: 12px; border-radius: 6px 0 0 6px;
    background: linear-gradient(180deg, #d8d8d8, var(--track-light)); box-shadow: inset 0 1px 2px rgba(0,0,0,0.3);
  }
  .zoom-thumb {
    position: absolute; left: 163px; top: 2px; width: 24px; height: 24px; border-radius: 5px;
    background: linear-gradient(180deg, #ffffff, #b5b5b5); border: 1px solid #8a8a8a;
  }

  .bottom-bar {
    position: absolute; left: 0; top: 1075px; width: 676px; height: 125px;
    background: linear-gradient(180deg, var(--bar-red-light), var(--bar-red) 40%, var(--bar-red-deep));
  }
  .bottom-bar::before {
    content: ""; position: absolute; left: 0; right: 0; top: 8px; border-top: 2px dashed var(--stitch);
  }
  .cancel-button {
    position: absolute; left: 30px; top: 36px; width: 89px; height: 48px; border-radius: 8px;
    background: linear-gradient(180deg, #ffffff, #d6d6d6); border: 1px solid #6d0d12;
    font-family: inherit; font-size: 21px; font-weight: 700; color: var(--button-text);
    box-shadow: 0 1px 2px rgba(0,0,0,0.5);
  }
  .bar-icon { position: absolute; }
</style>
</head>
<body>
<main class="capture-screen">
  <div class="viewfinder" role="img" aria-label="Live camera preview of an office desk with a laptop, cables and a pinboard"></div>

  <svg class="viewfinder-grid" viewBox="0 0 676 1062" aria-hidden="true">
    <g stroke="var(--grid-line)" stroke-width="1.5" fill="none">
      <rect x="3" y="5" width="670" height="1055"/>
      <line x1="224" y1="0" x2="224" y2="1062"/>
      <line x1="449" y1="0" x2="449" y2="1062"/>
      <line x1="0" y1="352" x2="676" y2="352"/>
      <line x1="0" y1="702" x2="676" y2="702"/>
    </g>
  </svg>

  <p class="grid-status">Grid Active</p>

  <div class="zoom-control">
    <span class="zoom-value">1.5x</span>
    <div class="zoom-track">
      <div class="zoom-track-empty"></div>
      <div class="zoom-track-fill"></div>
      <div class="zoom-thumb"></div>
    </div>
  </div>

  <nav class="bottom-bar">
    <button class="cancel-button">Cancel</button>

    <svg class="bar-icon shutter-icon" style="left:270px;top:10px" width="84" height="84" viewBox="0 0 84 84" aria-label="Capture">
      <g fill="none" stroke="var(--icon-silver)" stroke-width="4">
        <rect x="20" y="4" width="44" height="20" rx="7"/>
        <rect x="4" y="18" width="76" height="60" rx="14"/>
        <circle cx="42" cy="48" r="21"/>
        <circle cx="42" cy="48" r="11"/>
      </g>
    </svg>

    <svg class="bar-icon filter-icon" style="left:459px;top:37px" width="44" height="44" viewBox="0 0 44 44" aria-label="Filters">
      <g fill="var(--icon-silver)">
        <path d="M22 2 A20 20 0 0 1 39 12 L27 17 Z"/>
        <path d="M42 22 A20 20 0 0 1 32 39 L27 27 Z"/>
        <path d="M22 42 A20 20 0 0 1 5 32 L17 27 Z"/>
        <path d="M2 22 A20 20 0 0 1 12 5 L17 17 Z"/>
      </g>
      <circle cx="22" cy="22" r="6" fill="var(--bar-red)"/>
    </svg>

    <svg class="bar-icon settings-icon" style="left:600px;top:33px" width="46" height="46" viewBox="0 0 46 46" aria-label="Settings">
      <g fill="var(--icon-silver)">
        <circle cx="23" cy="23" r="15"/>
        <g>
          <rect x="19" y="1" width="8" height="10" rx="1"/>
          <rect x="19" y="35" width="8" height="10" rx="1"/>
          <rect x="1" y="19" width="10" height="8" rx="1"/>
          <rect x="35" y="19" width="10" height="8" rx="1"/>
        </g>
        <g transform="rotate(45 23 23)">
          <rect x="19" y="1" width="8" height="10" rx="1"/>
          <rect x="19" y="35" width="8" height="10" rx="1"/>
          <rect x="1" y="19" width="10" height="8" rx="1"/>
          <rect x="35" y="19" width="10" height="8" rx="1"/>
        </g>
      </g>
      <circle cx="23" cy="23" r="6" fill="var(--bar-red)"/>
    </svg>
  </nav>
</main>
</body>
</html>
```